Create a proposal + product powerpoint

Please see the powerpoint for the slides. There are about 20 slides to be created. Rest of them are for reference and show the design that I like.

I would like to move fast on this, since I need to present it next week (in the week of April 21st).

Please download the current content from here:
https://www.parcelbrook.net/fetch/qRtVmXzLwPkNbYcD

Please make at least 4 slides with the specific content so I can assess your design style.

Target Market(s)

Business Audience and very senior technical audience
Decision Makers

Industry/Entity Type

Product

Colors
e34297
a64599

Requirements
Must have
• Should be very clean, crisp.

I like to use Icons as shown in the powerpoint.... Please see the appendix of the slide deck that shows the various icons. Most of them just have plain text, and I would like to organize so that it does not look like some is just reading text.

I would like to focus on the design aspects so that the audience is clear on how the solution works.

Every page should some graphic element based on the slides shown in the appendix.

```html
<!DOCTYPE html>
<html lang="en">
<head>
<meta charset="utf-8">
<title>Benefits</title>
<link rel="stylesheet" href="https://fonts.googleapis.com/css2?family=Roboto+Condensed:wght@400;500&display=swap">
<style>
  :root {
    --brand-purple: #9a1fa3;
    --icon-dark: #5a1a5e;
    --icon-mid: #7a2d7e;
    --text-dark: #111111;
    --rule-grey: #d6d6d6;
    --logo-grey: #8a8a8a;
    --footer-left-a: #9c1f5f;
    --footer-left-b: #9a1f6d;
    --footer-right: #a4409f;
    --facet-light: #f3d6f3;
    --facet-deep: #c85ad6;
  }
  * { box-sizing: border-box; margin: 0; padding: 0; }
  html, body { width: 1200px; height: 900px; overflow: hidden; background: #ffffff; }
  body { font-family: "Roboto Condensed", "Arial Narrow", sans-serif; }

  .slide { position: relative; width: 1200px; height: 900px; overflow: hidden; background: #ffffff; }

  .facet-backdrop { position: absolute; inset: 0; width: 1200px; height: 900px; }

  .slide-title {
    position: absolute; left: 40px; top: 14px;
    font-size: 54px; font-weight: 400; color: var(--brand-purple);
    letter-spacing: -0.5px;
  }
  .header-rule {
    position: absolute; left: 42px; right: 0; top: 90px;
    height: 3px; background: var(--rule-grey);
  }
  .logo-placeholder {
    position: absolute; left: 1035px; top: 9px; width: 150px; height: 72px;
    border: 2px solid #ececec; border-radius: 8px; background: #ffffff;
    box-shadow: 0 1px 4px rgba(0,0,0,0.12);
    display: flex; align-items: center; justify-content: center;
    font-size: 30px; color: var(--logo-grey); letter-spacing: 1px;
  }

  .benefit-list { list-style: none; }
  .benefit {
    position: absolute; left: 52px; height: 142px;
    display: flex; align-items: center;
  }
  .benefit-icon {
    width: 146px; height: 142px; border-radius: 6px;
    background: radial-gradient(circle at 50% 45%, var(--icon-mid), var(--icon-dark) 80%);
    display: flex; align-items: center; justify-content: center;
    box-shadow: 0 1px 3px rgba(0,0,0,0.25);
  }
  .benefit-icon svg { width: 96px; height: 96px; }
  .benefit-text {
    margin-left: 32px; font-size: 37px; color: var(--text-dark);
    letter-spacing: 0.6px;
  }
  .benefit--results { top: 141px; }
  .benefit--compliance { top: 312px; }
  .benefit--visibility { top: 490px; }
  .benefit--productivity { top: 673px; }

  .footer { position: absolute; left: 0; bottom: 0; width: 1200px; height: 60px; }
  .footer svg { position: absolute; inset: 0; }
  .footer-page, .footer-copy {
    position: absolute; top: 0; height: 60px; display: flex; align-items: center;
    color: #ffffff; font-size: 24px; letter-spacing: 0.5px;
  }
  .footer-page { left: 13px; }
  .footer-copy { right: 14px; }
</style>
</head>
<body>
<main class="slide">
  <svg class="facet-backdrop" viewBox="0 0 1200 900" role="img" aria-label="Decorative faceted triangle pattern in soft pink and violet">
    <defs>
      <linearGradient id="facetFade" x1="0" y1="0" x2="1" y2="0">
        <stop offset="0" stop-color="#ffffff" stop-opacity="0"/>
        <stop offset="0.3" stop-color="var(--facet-light)"/>
        <stop offset="1" stop-color="var(--facet-deep)"/>
      </linearGradient>
      <radialGradient id="leftHaze" cx="0.5" cy="0.5" r="0.5">
        <stop offset="0" stop-color="#e9c7ee" stop-opacity="0.8"/>
        <stop offset="1" stop-color="#ffffff" stop-opacity="0"/>
      </radialGradient>
    </defs>
    <ellipse cx="20" cy="600" rx="160" ry="200" fill="url(#leftHaze)"/>
    <polygon points="930,93 1200,93 1200,840 880,840 1020,560 900,300" fill="url(#facetFade)"/>
  </svg>

  <h1 class="slide-title">Benefits</h1>
  <div class="header-rule"></div>
  <div class="logo-placeholder">LOGO HERE</div>

  <ul class="benefit-list">
    <li class="benefit benefit--results">
      <span class="benefit-icon">
        <svg viewBox="0 0 100 100" aria-hidden="true">
          <circle cx="46" cy="54" r="36" fill="none" stroke="#fff" stroke-width="8"/>
          <circle cx="46" cy="54" r="22" fill="none" stroke="#fff" stroke-width="7"/>
          <circle cx="46" cy="54" r="8" fill="#fff"/>
          <line x1="46" y1="54" x2="82" y2="18" stroke="#fff" stroke-width="5"/>
          <polygon points="78,10 90,10 90,22 84,22 84,16 78,16" fill="#fff"/>
        </svg>
      </span>
      <span class="benefit-text">Consistent, predictable, repeatable results</span>
    </li>
    <li class="benefit benefit--compliance">
      <span class="benefit-icon">
        <svg viewBox="0 0 100 100" aria-hidden="true">
          <polygon points="50,6 94,26 6,26" fill="#fff"/>
          <rect x="10" y="30" width="80" height="6" fill="#fff"/>
          <rect x="16" y="40" width="9" height="38" fill="#fff"/>
          <rect x="34" y="40" width="9" height="38" fill="#fff"/>
          <rect x="57" y="40" width="9" height="38" fill="#fff"/>
          <rect x="75" y="40" width="9" height="38" fill="#fff"/>
          <rect x="8" y="82" width="84" height="5" fill="#fff"/>
          <rect x="2" y="90" width="96" height="6" fill="#fff"/>
        </svg>
      </span>
      <span class="benefit-text">Meet your compliance and governance requirements</span>
    </li>
    <li class="benefit benefit--visibility">
      <span class="benefit-icon">
        <svg viewBox="0 0 100 100" aria-hidden="true">
          <path d="M72 28 A36 36 0 1 0 84 60" fill="none" stroke="#fff" stroke-width="8"/>
          <polyline points="28,52 44,68 90,14" fill="none" stroke="#fff" stroke-width="11" stroke-linejoin="round"/>
        </svg>
      </span>
      <span class="benefit-text">Full visibility into change management processes</span>
    </li>
    <li class="benefit benefit--productivity">
      <span class="benefit-icon">
        <svg viewBox="0 0 100 100" aria-hidden="true">
          <rect x="22" y="12" width="16" height="16" fill="#fff"/>
          <rect x="62" y="12" width="16" height="16" fill="#fff"/>
          <polygon points="18,32 42,32 44,90 6,90 6,60" fill="#fff"/>
          <polygon points="58,32 82,32 94,60 94,90 56,90" fill="#fff"/>
          <rect x="42" y="42" width="16" height="20" fill="#fff"/>
        </svg>
      </span>
      <span class="benefit-text">Improved developer productivity</span>
    </li>
  </ul>

  <footer class="footer">
    <svg viewBox="0 0 1200 60" aria-hidden="true">
      <defs>
        <linearGradient id="footerLeft" x1="0" y1="0" x2="1" y2="0">
          <stop offset="0" stop-color="var(--footer-left-a)"/>
          <stop offset="1" stop-color="var(--footer-left-b)"/>
        </linearGradient>
      </defs>
      <polygon points="0,0 908,0 938,60 0,60" fill="url(#footerLeft)"/>
      <polygon points="918,0 1200,0 1200,60 948,60" fill="var(--footer-right)"/>
    </svg>
    <span class="footer-page">Page : 01</span>
    <span class="footer-copy">Copyright text here</span>
  </footer>
</main>
</body>
</html>
```